Business card design Needed for new logo / Construction business, home extensions and new builds

We need a business card design using our new logo files which i will attach to this project :)

We are a small construction business specialising in home extensions, new builds and property development. We are very ambitious and would appreciate professional and elegant designs for our new business card.

Very serious about using the services on MakerQuarry and recently acquired our new logo from here :)

Please get involved, i will feedback when i can as i am very busy but can respond daily, thanks

Target Market(s)

People that want to build onto their houses, new building developments or adding too their existing property

Industry/Entity Type

Construction

Contact Information for Business Card

Renwick Tolliver Construction, Lionel Ashby (Managing Director), Tel 07822254961, email - info@renwick-tolliver, www.renwick-tolliver.co.uk

Colors

Designer to choose colors to be used in the design.

Requirements
Must have
• I like a deep grey on the back please. A lot of you have provided black from and back, try mixing things up a little. The black looks cool 😎 Thanks

```html
<!DOCTYPE html>
<html lang="en">
<head>
<meta charset="utf-8">
<title>Renwick Tolliver Construction – Business Card</title>
<link href="https://fonts.googleapis.com/css2?family=Open+Sans:wght@400;600;700&display=swap" rel="stylesheet">
<style>
  :root {
    --stage: #232323;
    --card: #1e1e21;
    --card-back: #19191b;
    --gold: #d9a93a;
    --gold-light: #f3cf6e;
    --silver: #d6d6d8;
    --white: #f2f2f2;
    --ink: #1b1b1d;
  }
  * { box-sizing: border-box; margin: 0; padding: 0; }
  html, body { width: 1200px; height: 780px; overflow: hidden; }
  body {
    background: var(--stage);
    font-family: "Open Sans", Arial, sans-serif;
    position: relative;
  }
  .card {
    position: absolute;
    top: 70px;
    width: 380px;
    height: 640px;
    border-radius: 26px;
    overflow: hidden;
  }
  .card--back { left: 170px; background: var(--card-back); }
  .card--front { left: 650px; background: var(--card); }

  .back-pattern {
    position: absolute; inset: 0;
    background: linear-gradient(135deg, #3a3a3d 0%, #262628 35%, #1a1a1c 60%, #141415 100%);
  }
  .back-name {
    position: absolute;
    left: 50%; top: 50%;
    transform: translate(-50%, -50%) rotate(90deg);
    display: flex; align-items: center; gap: 14px;
    white-space: nowrap;
    color: var(--gold);
    font-weight: 600;
    font-size: 22px;
    letter-spacing: 2px;
    text-transform: uppercase;
  }
  .brand-square { width: 26px; height: 26px; background: var(--gold); flex: none; }

  .front-brand {
    position: absolute;
    top: 110px; left: 0; right: 0;
    display: flex; flex-direction: column; align-items: center; gap: 14px;
  }
  .front-brand .brand-square { width: 40px; height: 40px; }
  .front-brand-name {
    color: var(--gold);
    font-weight: 600;
    font-size: 19px;
    letter-spacing: 2px;
    text-transform: uppercase;
    text-align: center;
    line-height: 1.4;
  }

  .contact-block {
    position: absolute;
    top: 330px; left: 20px; right: 20px;
    text-align: center;
  }
  .person-name { font-weight: 700; font-size: 30px; line-height: 1.1; }
  .person-first { color: var(--silver); }
  .person-last { color: var(--gold-light); }
  .person-role { color: var(--white); font-size: 14px; font-weight: 600; margin-top: 2px; }
  .dot-row { display: block; margin: 12px auto 8px; }
  .contact-lines { color: var(--white); font-size: 15px; line-height: 1.45; }
  .address { color: var(--white); font-size: 15px; line-height: 1.45; }
</style>
</head>
<body>

<section class="card card--back" aria-label="Card back">
  <div class="back-pattern" role="img" aria-label="Repeating tonal pattern of the company mark in dark grey"></div>
  <div class="back-name"><span class="brand-square"></span>Renwick Tolliver Construction</div>
</section>

<section class="card card--front" aria-label="Card front">
  <div class="front-brand">
    <span class="brand-square"></span>
    <div class="front-brand-name">Renwick Tolliver<br>Construction</div>
  </div>

  <div class="contact-block">
    <h1 class="person-name"><span class="person-first">Lionel</span> <span class="person-last">Ashby</span></h1>
    <p class="person-role">Managing Director</p>

    <svg class="dot-row" width="340" height="32" viewBox="0 0 340 32" aria-hidden="true">
      <defs>
        <linearGradient id="gold-a" x1="0" y1="0" x2="1" y2="1">
          <stop offset="0" stop-color="#f6d77c"/><stop offset="1" stop-color="#c08a25"/>
        </linearGradient>
      </defs>
      <g fill="url(#gold-a)">
        <circle cx="8" cy="16" r="2"/><circle cx="22" cy="16" r="2.5"/><circle cx="37" cy="16" r="3"/>
        <circle cx="53" cy="16" r="4"/><circle cx="71" cy="16" r="5"/><circle cx="91" cy="16" r="6"/>
        <circle cx="130" cy="16" r="14"/><circle cx="170" cy="16" r="14"/><circle cx="210" cy="16" r="14"/>
        <circle cx="249" cy="16" r="6"/><circle cx="269" cy="16" r="5"/><circle cx="287" cy="16" r="4"/>
        <circle cx="303" cy="16" r="3"/><circle cx="318" cy="16" r="2.5"/><circle cx="332" cy="16" r="2"/>
      </g>
      <g fill="none" stroke="var(--ink)" stroke-width="1.6" stroke-linecap="round" stroke-linejoin="round">
        <path d="M124 10c0 7 5 12 12 12l2-3-3-2-2 1c-2-1-4-3-5-5l1-2-2-3z"/>
        <rect x="162" y="10" width="16" height="12" rx="1"/><path d="M162 11l8 6 8-6"/>
        <circle cx="210" cy="16" r="7"/><ellipse cx="210" cy="16" rx="3" ry="7"/><path d="M203 16h14"/>
      </g>
    </svg>

    <p class="contact-lines">0782 225 4961<br>info@renwick-tolliver.co.uk<br>www.renwick-tolliver.co.uk</p>

    <svg class="dot-row" width="340" height="32" viewBox="0 0 340 32" aria-hidden="true">
      <defs>
        <linearGradient id="gold-b" x1="0" y1="0" x2="1" y2="1">
          <stop offset="0" stop-color="#f6d77c"/><stop offset="1" stop-color="#c08a25"/>
        </linearGradient>
      </defs>
      <g fill="url(#gold-b)">
        <circle cx="8" cy="16" r="2"/><circle cx="23" cy="16" r="2.5"/><circle cx="39" cy="16" r="3"/>
        <circle cx="56" cy="16" r="4"/><circle cx="75" cy="16" r="5"/><circle cx="96" cy="16" r="6"/>
        <circle cx="119" cy="16" r="7"/><circle cx="143" cy="16" r="8"/>
        <circle cx="170" cy="16" r="14"/>
        <circle cx="197" cy="16" r="8"/><circle cx="221" cy="16" r="7"/><circle cx="244" cy="16" r="6"/>
        <circle cx="265" cy="16" r="5"/><circle cx="284" cy="16" r="4"/><circle cx="301" cy="16" r="3"/>
        <circle cx="317" cy="16" r="2.5"/><circle cx="332" cy="16" r="2"/>
      </g>
      <g fill="none" stroke="var(--ink)" stroke-width="1.6" stroke-linejoin="round">
        <path d="M170 24c-4-5-6-8-6-11a6 6 0 0 1 12 0c0 3-2 6-6 11z"/>
        <circle cx="170" cy="13" r="2"/>
      </g>
    </svg>

    <p class="address">Linden Road, Fairholm<br>Westbury, BH7 2RN</p>
  </div>
</section>

</body>
</html>
```